The Korvane LLC Asset Classes

I'm looking for for two designs here to go into powerpoint and potentially as a standalone PDF. My company does wealth management.
Graphic Image #1
I break down the investment world into 4 broad categories
-Preservation
-Capital Markets
-Real Estate
-Alternatives
In each broad category, there are subcategories:
Preservation: cash, checking/savings accounts, money market accounts, CD's, and fixed annuities.
Capital Markets: Publicly traded stocks and bonds
Real Estate: single-family residence, retail, industrial, multifamily, and office
Alternatives: private equity, private credit, cryptocurrency, asset-backed loans, tax liens, oil & gas, litigation finance, and royalties
Graphic 2: Please see the bottom f page 1 of the Tessolin Decks PDF.
Just like in graphic one, you have 4 categories of the Capital Markets and their respective subcategories
Category 1: Domestic Stocks: Subcategories are Large, mid, and small size companies
Category 2: International Stocks: Subcategories are Large, Mid/Small and by region - Developed and Emerging
Category 3: Fixed Income: You have subcategories like corporate, municipal, government, domestic, international
Category 4: Alternatives: The subcategories are metals and real estate
---------------------
I'm looking to create a graphic (either pie chart, or a circle broken into parts or some other clever way to illustrate this) to clearly illustrate both of these universes in a clean, professional, slick manner.
Target Market(s)
Investors
Colors
Designer to choose colors to be used in the design.
Requirements
Must have
- Clean
- professional
- Easy to read
- Creative
- Visually appealling
Nice to have
- I have attached my logo and some marketing materials so you can get a feel of what I am doing. Maybe you can clean this up too!

```html
<!DOCTYPE html>
<html lang="en">
<head>
<meta charset="utf-8">
<title>Korvane LLC – Capital Markets Categories</title>
<link href="https://fonts.googleapis.com/css2?family=Fira+Sans:wght@300&family=Nunito:wght@800&family=Source+Sans+3:wght@400;600&display=swap" rel="stylesheet">
<style>
  :root {
    --page-bg: #dcdddf;
    --slide-bg: #ffffff;
    --brand-blue: #0b5f86;
    --accent-orange: #e8922b;
    --panel-orange: #ecae62;
    --navy: #003262;
    --ocean: #0868ae;
    --sky: #17a3de;
    --mist: #74c0e0;
    --text-dark: #4a4a4a;
  }
  * { margin: 0; padding: 0; box-sizing: border-box; }
  html, body {
    width: 1200px; height: 1000px; overflow: hidden;
    background: var(--page-bg);
  }
  .slide {
    position: absolute; left: 0; top: 163px;
    width: 1200px; height: 674px;
    background: var(--slide-bg);
  }
  .brand {
    position: absolute; left: 74px; top: 100px;
    display: flex; align-items: center; gap: 12px;
    font-family: "Fira Sans", sans-serif; font-weight: 300;
    font-size: 40px; color: var(--brand-blue); letter-spacing: 0.5px;
  }
  .brand-dot {
    width: 22px; height: 22px; border-radius: 50%;
    background: var(--accent-orange);
  }
  .title-panel {
    position: absolute; left: 74px; top: 223px;
    width: 313px; height: 373px;
    background: var(--panel-orange);
  }
  .title-panel h1 {
    position: absolute; left: 36px; top: 34px;
    font-family: "Fira Sans", sans-serif; font-weight: 300;
    font-size: 47px; line-height: 54px; color: #ffffff;
  }
  .chart { position: absolute; left: 0; top: 0; }
  .segment-label {
    font-family: "Nunito", sans-serif; font-weight: 800;
    font-size: 16px; fill: #ffffff; text-anchor: middle;
  }
  .sublist {
    position: absolute; list-style: none;
    font-family: "Source Sans 3", sans-serif; font-size: 12.5px;
    line-height: 15px; color: var(--text-dark);
  }
  .sublist li { padding-left: 9px; text-indent: -9px; }
  .sublist li::before { content: "• "; }
  .sublist--domestic { left: 525px; top: 207px; width: 90px; }
  .sublist--international { left: 1001px; top: 190px; width: 150px; }
  .sublist--alternatives { left: 525px; top: 475px; }
  .sublist--fixed { left: 991px; top: 475px; }
</style>
</head>
<body>
<section class="slide">
  <div class="brand"><span class="brand-dot"></span>Korvane LLC</div>

  <div class="title-panel">
    <h1>Capital<br>Markets<br>Categories</h1>
  </div>

  <svg class="chart" width="1200" height="674" viewBox="0 0 1200 674" aria-label="Capital markets categories chart">
    <defs>
      <filter id="soft-shadow" x="-30%" y="-30%" width="160%" height="160%">
        <feDropShadow dx="-6" dy="14" stdDeviation="14" flood-color="#000" flood-opacity="0.22"/>
      </filter>
      <radialGradient id="hub-fill" cx="35%" cy="30%" r="75%">
        <stop offset="0" stop-color="#ffffff"/>
        <stop offset="1" stop-color="#d2d3d5"/>
      </radialGradient>
    </defs>

    <line class="divider" x1="692" y1="79" x2="1198" y2="79" stroke="var(--accent-orange)" stroke-width="1.3" stroke-dasharray="3 3"/>
    <line class="divider" x1="467" y1="596" x2="1198" y2="596" stroke="var(--accent-orange)" stroke-width="1.3" stroke-dasharray="3 3"/>

    <g class="connectors" stroke="var(--accent-orange)" stroke-width="1" fill="none">
      <polyline points="549,186 670,186"/>
      <polyline points="893,165 1042,165 1042,184"/>
      <polyline points="650,437 552,437 552,456"/>
      <polyline points="944,458 1022,458"/>
    </g>
    <g class="connector-dots" fill="var(--accent-orange)">
      <circle cx="549" cy="186" r="2.5"/>
      <circle cx="1042" cy="184" r="2.5"/>
      <circle cx="552" cy="456" r="2.5"/>
      <circle cx="1022" cy="458" r="2.5"/>
    </g>

    <g class="segments" filter="url(#soft-shadow)">
      <path d="M811,338 L811,526 A188,188 0 0 1 623,338 Z" fill="var(--sky)"/>
      <path d="M811,338 L991,338 A180,180 0 0 1 811,518 Z" fill="var(--mist)"/>
      <path d="M811,338 L811,142 A196,196 0 0 1 1007,338 Z" fill="var(--ocean)"/>
      <path d="M811,338 L603,338 A208,208 0 0 1 811,130 Z" fill="var(--navy)"/>
    </g>

    <text class="segment-label" x="707" y="243">Domestic<tspan x="707" dy="18">Stocks</tspan></text>
    <text class="segment-label" x="894" y="243">International<tspan x="894" dy="18">Stocks</tspan></text>
    <text class="segment-label" x="726" y="434">Alternatives</text>
    <text class="segment-label" x="896" y="426">Fixed<tspan x="896" dy="18">Income</tspan></text>

    <g class="hub" filter="url(#soft-shadow)">
      <circle cx="811" cy="338" r="76" fill="#ececed"/>
    </g>
    <circle cx="811" cy="338" r="67" fill="url(#hub-fill)" stroke="var(--accent-orange)" stroke-width="2"/>
  </svg>

  <ul class="sublist sublist--domestic">
    <li>Large</li><li>Mid</li><li>Small Size Companies</li>
  </ul>
  <ul class="sublist sublist--international">
    <li>Large</li><li>Mid/Small</li><li>By Region (Developed and Emerging)</li>
  </ul>
  <ul class="sublist sublist--alternatives">
    <li>Metals</li><li>Real Estate</li>
  </ul>
  <ul class="sublist sublist--fixed">
    <li>Corporate</li><li>Municipal</li><li>Government</li><li>Domestic</li><li>International</li>
  </ul>
</section>
</body>
</html>
```